SaaS Early tech startup business card design

Unique design for experience ecommerce platform company. the business cards will be used by executive members. conformance with color code is required.

```html
<!DOCTYPE html>
<html lang="en">
<head>
<meta charset="utf-8">
<title>novra — business cards</title>
<link rel="stylesheet" href="https://fonts.googleapis.com/css2?family=Roboto:wght@400;500;700;900&display=swap">
<style>
  :root {
    --bg: #6b6868;
    --teal-light: #14a393;
    --teal: #12877f;
    --teal-dark: #0c6a6e;
    --navy-teal: #0d4d78;
    --edge: #0a5663;
    --paper: #f4f5f5;
    --ink: #222626;
    --accent: #137e7b;
    --white: #ffffff;
  }
  * { margin: 0; padding: 0; box-sizing: border-box; }
  html, body { width: 1200px; height: 1200px; overflow: hidden; }
  body {
    background: var(--bg);
    position: relative;
    font-family: "Roboto", Arial, sans-serif;
  }
  .card {
    position: absolute;
    left: 303px;
    width: 594px;
    height: 350px;
    border-radius: 22px;
    overflow: hidden;
  }
  .card--front { top: 198px; }
  .card--back { top: 636px; background: var(--paper); }
  .card svg.card__bg { position: absolute; inset: 0; width: 100%; height: 100%; }

  .brand {
    position: absolute;
    text-align: center;
    color: var(--white);
  }
  .brand__name {
    font-family: "Roboto", Arial, sans-serif;
    font-weight: 900;
    font-size: 96px;
    line-height: 1;
    letter-spacing: -1px;
    display: block;
  }
  .brand__tagline {
    display: block;
    font-weight: 400;
    font-size: 15px;
    letter-spacing: 5.5px;
    margin-top: 6px;
    padding-left: 5px;
  }
  .card--front .brand { left: 0; right: 0; top: 118px; }
  .card--back .brand { left: 21px; width: 262px; top: 112px; }
  .card--back .brand__name { font-size: 86px; }
  .card--back .brand__tagline { font-size: 14px; letter-spacing: 5px; }

  .contact {
    position: absolute;
    left: 360px;
    top: 80px;
    color: var(--ink);
  }
  .contact__name {
    font-weight: 700;
    font-size: 23px;
    color: var(--accent);
    letter-spacing: -0.3px;
  }
  .contact__role { font-size: 15px; margin-top: 2px; }
  .contact__list { list-style: none; margin-top: 24px; }
  .contact__list li {
    display: flex;
    align-items: center;
    gap: 14px;
    font-size: 15.5px;
    height: 22.5px;
  }
  .contact__list svg { width: 15px; height: 15px; fill: var(--accent); flex: none; }
  .contact__address { font-size: 15.5px; line-height: 22.5px; margin-top: 8px; }

  .card__decor {
    position: absolute;
    right: 8px;
    bottom: 8px;
    width: 56px;
    height: 62px;
    border-radius: 12px;
    background: linear-gradient(135deg, rgba(19,126,123,0.05), rgba(19,126,123,0.18));
  }
</style>
</head>
<body>

  <section class="card card--front">
    <svg class="card__bg" viewBox="0 0 594 350" preserveAspectRatio="none" aria-hidden="true">
      <defs>
        <linearGradient id="frontBase" x1="0" y1="0" x2="1" y2="1">
          <stop offset="0" stop-color="#13998c"/>
          <stop offset="1" stop-color="#0c676c"/>
        </linearGradient>
      </defs>
      <rect width="594" height="350" fill="url(#frontBase)"/>
      <path d="M0 0 H594 V20 C560 110 470 100 400 70 C300 25 200 -10 0 40 Z" fill="#16958a" opacity="0.9"/>
      <path d="M0 240 C40 170 100 130 160 138 C260 150 270 300 380 320 C460 335 540 330 594 350 H0 Z" fill="#12a092"/>
      <path d="M0 300 C60 250 130 240 200 280 C250 310 300 340 340 350 H0 Z" fill="#14a393" opacity="0.6"/>
    </svg>
    <div class="brand">
      <span class="brand__name">novra</span>
      <span class="brand__tagline">BUILT AROUND YOU</span>
    </div>
  </section>

  <section class="card card--back">
    <svg class="card__bg" viewBox="0 0 594 350" preserveAspectRatio="none" aria-hidden="true">
      <defs>
        <linearGradient id="backPanel" x1="0" y1="0" x2="0.6" y2="1">
          <stop offset="0" stop-color="#119d8f"/>
          <stop offset="0.55" stop-color="#0e7478"/>
          <stop offset="1" stop-color="#0d4d78"/>
        </linearGradient>
      </defs>
      <path d="M263 0 H290 C330 80 338 220 270 350 H259 C325 200 302 70 263 0 Z" fill="#0a5663" opacity="0.85"/>
      <path d="M0 0 H263 C302 70 325 200 259 350 H0 Z" fill="url(#backPanel)"/>
    </svg>
    <div class="brand">
      <span class="brand__name">novra</span>
      <span class="brand__tagline">BUILT AROUND YOU</span>
    </div>

    <div class="contact">
      <h1 class="contact__name">Karim D.</h1>
      <p class="contact__role">CTO/Owner</p>
      <ul class="contact__list">
        <li>
          <svg viewBox="0 0 24 24"><path d="M6.6 10.8a15.1 15.1 0 0 0 6.6 6.6l2.2-2.2c.3-.3.7-.4 1-.2 1.1.4 2.3.6 3.6.6.6 0 1 .4 1 1V20c0 .6-.4 1-1 1C10.6 21 3 13.4 3 4c0-.6.4-1 1-1h3.5c.6 0 1 .4 1 1 0 1.3.2 2.5.6 3.6.1.3 0 .7-.2 1z"/></svg>
          (00) 0111 NOVRA
        </li>
        <li>
          <svg viewBox="0 0 24 24"><path d="M2 5h20v14H2z M4 7v.4l8 5.3 8-5.3V7z" fill-rule="evenodd"/></svg>
          info@novra.net
        </li>
        <li>
          <svg viewBox="0 0 24 24"><path d="M12 2a10 10 0 1 0 0 20 10 10 0 0 0 0-20zm6.9 6h-3a15.6 15.6 0 0 0-1.3-3.6A8 8 0 0 1 18.9 8zM12 4c.8 1.2 1.5 2.5 1.9 4h-3.8c.4-1.5 1.1-2.8 1.900-4zM4.3 14a8.2 8.2 0 0 1 0-4h3.4a16.5 16.5 0 0 0 0 4zm.8 2h3c.3 1.3.8 2.5 1.3 3.6A8 8 0 0 1 5.1 16zm3-8h-3a8 8 0 0 1 4.3-3.6C8.9 5.5 8.4 6.7 8.1 8zM12 20c-.8-1.2-1.5-2.5-1.9-4h3.8c-.4 1.5-1.1 2.8-1.9 4zm2.3-6H9.7a14.7 14.7 0 0 1 0-4h4.6a14.7 14.7 0 0 1 0 4zm.3 5.6c.5-1.1 1-2.3 1.3-3.6h3a8 8 0 0 1-4.3 3.6zm1.7-5.6a16.5 16.5 0 0 0 0-4h3.4a8.2 8.2 0 0 1 0 4z"/></svg>
          www.novra.net
        </li>
      </ul>
      <p class="contact__address">Meridian Tower, Dubai<br>Dubai Tech Quarter, UAE</p>
    </div>

    <div class="card__decor" role="img" aria-label="Faint line-art brand decoration"></div>
  </section>

</body>
</html>
```